Professional Business Card - TWO SIDES

I need a new business card design to be used by myself and my employees. I would like a professional card and for the front I thought I would like a dark blue thatch with our logo in a raised gold foil on top of it. On the other side I would like name, position, and contact info. I've uploaded our old design for an example of the info used.

Target Market(s)

Business Clients

Industry/Entity Type

CPA Firm

Contact Information for Business Card

Logo, Name, Title, Address, Phone Numbers, Website address, Email Address

Font styles to use
Serif
Sans Serif

Colors
0054AA
0677BA
7BADD7
CADEEF
E8F1F8
0094D4
00A9DD
6FCCEA
C7EBF8
E9F6FB

Requirements
Must have
• Modern Professional Look
Nice to have
• Logo in Gold Foil or ability to have is raised. I like our logo in a single color
Should not have
• I've uploaded old business card

```html
<!DOCTYPE html>
<html lang="en">
<head>
<meta charset="utf-8">
<title>Hale &amp; Hale — Business Card</title>
<link href="https://fonts.googleapis.com/css2?family=Arimo:wght@400;700&display=swap" rel="stylesheet">
<style>
  :root {
    --backdrop: #2a2a2c;
    --navy: #173461;
    --gold: #c99a36;
    --paper: #ffffff;
    --ink: #1f1f1f;
  }
  * { box-sizing: border-box; margin: 0; padding: 0; }
  html, body {
    width: 1200px; height: 900px; overflow: hidden;
    background: var(--backdrop);
  }
  .canvas {
    position: relative; width: 1200px; height: 900px;
    display: flex; flex-direction: column; align-items: center;
    justify-content: center; gap: 40px;
  }
  .card {
    position: relative; width: 660px; height: 380px;
    border-radius: 22px; overflow: hidden;
    box-shadow: 0 14px 30px rgba(0,0,0,.45);
  }

  /* Brand name block */
  .brand {
    display: flex; align-items: center; gap: 16px;
    font-family: "Arimo", sans-serif; font-weight: 700; line-height: 1;
  }
  .brand-dot { border-radius: 50%; flex: none; }

  /* Front side */
  .card-front {
    background: var(--navy);
    display: flex; align-items: center; justify-content: center;
  }
  .card-front .brand { font-size: 72px; color: var(--gold); }
  .card-front .brand-dot { width: 44px; height: 44px; background: var(--gold); }

  /* Back side */
  .card-back {
    background: var(--paper);
    display: flex; flex-direction: column; align-items: center;
    padding-top: 46px;
  }
  .card-back .brand { font-size: 46px; color: var(--navy); gap: 12px; }
  .card-back .brand-dot { width: 28px; height: 28px; background: var(--navy); }

  .person-name {
    margin-top: 30px;
    font-family: "Arimo", sans-serif; font-weight: 700;
    font-size: 26px; letter-spacing: 1px; color: var(--navy);
    text-transform: uppercase;
  }
  .person-title {
    font-family: "Arimo", sans-serif; font-size: 18px; color: var(--ink);
  }
  .contact-icons { display: flex; gap: 8px; margin-top: 10px; }
  .contact-icons svg { width: 24px; height: 24px; }
  .contact-lines {
    margin-top: 6px; text-align: center;
    font-family: "Arimo", sans-serif; font-size: 17px; line-height: 1.3; color: var(--ink);
  }
  .address-band {
    position: absolute; left: 0; right: 0; bottom: 0; height: 46px;
    background: var(--navy);
    display: flex; align-items: center; justify-content: center;
    font-family: "Arimo", sans-serif; font-size: 17px; color: var(--paper);
  }
</style>
</head>
<body>
<main class="canvas">

  <section class="card card-front" aria-label="Card front">
    <div class="brand"><span class="brand-dot"></span>Hale &amp; Hale</div>
  </section>

  <section class="card card-back" aria-label="Card back">
    <div class="brand"><span class="brand-dot"></span>Hale &amp; Hale</div>

    <div class="person-name">Daniel Reyes</div>
    <div class="person-title">Founder</div>

    <div class="contact-icons">
      <svg viewBox="0 0 24 24" aria-label="Phone">
        <circle cx="12" cy="12" r="11" fill="none" stroke="var(--navy)" stroke-width="1.5"/>
        <circle cx="12" cy="12" r="8.5" fill="var(--navy)"/>
        <path d="M8 9.5h8v1.5H8z M9 11.5h6l1 4H8z" fill="#fff"/>
      </svg>
      <svg viewBox="0 0 24 24" aria-label="Email">
        <circle cx="12" cy="12" r="11" fill="none" stroke="var(--navy)" stroke-width="1.5"/>
        <circle cx="12" cy="12" r="8.5" fill="var(--navy)"/>
        <rect x="7.5" y="9" width="9" height="6.5" fill="#fff"/>
        <path d="M7.5 9l4.5 3.5L16.5 9" fill="none" stroke="var(--navy)" stroke-width="1"/>
      </svg>
      <svg viewBox="0 0 24 24" aria-label="Website">
        <circle cx="12" cy="12" r="11" fill="none" stroke="var(--navy)" stroke-width="1.5"/>
        <circle cx="12" cy="12" r="8.5" fill="var(--navy)"/>
        <circle cx="12" cy="12" r="4.5" fill="none" stroke="#fff" stroke-width="1"/>
        <path d="M7.5 12h9 M12 7.5v9" stroke="#fff" stroke-width="1"/>
      </svg>
    </div>

    <div class="contact-lines">
      <div>(555) 014 2290</div>
      <div>info@halehale.com</div>
      <div>www.halehale.com</div>
    </div>

    <div class="address-band">1420 N. Carver Street Country Name, AB 10420</div>
  </section>

</main>
</body>
</html>
```